Business Card Design (NEW FILES)

ATTENTION: New vector files are available. Please update your design to reflect/use the new (better resolution) logo images.

Seeking a unique and professional business card design for a commercial drone photography/videography business. The layout should feature
the logo (attached) and include the following information:
Owen Tarrick
614-502-7738
www.skylarkreelworks.example
NRD Certified Remote Pilot

Owen Tarrick

```html
<!DOCTYPE html>
<html lang="en">
<head>
<meta charset="utf-8">
<title>Skylark Reelworks Business Card</title>
<link rel="stylesheet" href="https://fonts.googleapis.com/css2?family=Montserrat:wght@700&family=Open+Sans:wght@400;600&display=swap">
<style>
  :root {
    --stage: #232323;
    --navy: #141a4a;
    --navy-soft: #2a3170;
    --orange: #ee8a46;
    --gold: #c18428;
    --paper: #ffffff;
    --ink: #141a4a;
  }
  html, body {
    margin: 0;
    padding: 0;
    width: 1200px;
    height: 780px;
    overflow: hidden;
    background: var(--stage);
  }
  .canvas {
    position: relative;
    width: 1200px;
    height: 780px;
  }
  .card {
    position: absolute;
    top: 230px;
    width: 560px;
    height: 320px;
    border-radius: 18px;
    overflow: hidden;
  }
  .card-front { left: 30px; background: var(--paper); }
  .card-back { left: 610px; background: var(--navy); }
  .card-art { position: absolute; inset: 0; }
  .brand {
    position: absolute;
    display: flex;
    align-items: center;
    gap: 10px;
    font-family: "Open Sans", sans-serif;
    font-weight: 600;
    letter-spacing: 0.02em;
  }
  .brand-mark {
    width: 14px;
    height: 14px;
    border-radius: 50%;
    background: var(--orange);
  }
  .card-front .brand { left: 40px; top: 30px; font-size: 26px; color: var(--ink); }
  .card-back .brand {
    left: 0; right: 0; top: 138px;
    justify-content: center;
    font-size: 36px;
    color: var(--paper);
  }
  .card-back .brand-mark { width: 20px; height: 20px; }
  .contact-list {
    position: absolute;
    left: 44px;
    top: 92px;
    margin: 0;
    padding: 0;
    list-style: none;
    font-family: "Open Sans", sans-serif;
    font-size: 13px;
    color: var(--ink);
  }
  .contact-list li {
    display: flex;
    align-items: center;
    gap: 8px;
    height: 20px;
  }
  .contact-icon { width: 12px; height: 12px; flex: none; }
  .holder {
    position: absolute;
    right: 36px;
    top: 124px;
    text-align: right;
  }
  .holder-name {
    margin: 0;
    font-family: "Montserrat", sans-serif;
    font-weight: 700;
    font-size: 30px;
    line-height: 1.1;
  }
  .holder-first { color: var(--orange); }
  .holder-last { color: var(--navy); }
  .holder-role {
    margin: 2px 0 0;
    font-family: "Open Sans", sans-serif;
    font-size: 15px;
    color: var(--ink);
  }
  .credentials {
    position: absolute;
    left: 40px;
    bottom: 16px;
    margin: 0;
    font-family: "Open Sans", sans-serif;
    font-size: 15px;
    line-height: 1.45;
    color: var(--paper);
  }
</style>
</head>
<body>
<main class="canvas">

  <section class="card card-front" aria-label="Business card front">
    <svg class="card-art" width="560" height="320" viewBox="0 0 560 320">
      <path class="wave-navy" d="M0,120 C20,220 90,250 200,258 C300,266 360,290 400,320 L0,320 Z" fill="var(--navy)"/>
      <path class="wave-orange" d="M10,96 C20,176 70,222 160,244" fill="none" stroke="var(--orange)" stroke-width="5" stroke-linecap="round"/>
      <rect class="edge-tab" x="540" y="196" width="20" height="52" fill="var(--gold)"/>
      <rect class="drone-illustration" role="img" aria-label="Illustration of a camera drone in flight" x="320" y="205" width="150" height="100" rx="20" fill="var(--navy-soft)" opacity="0.35"/>
    </svg>

    <div class="brand"><span class="brand-mark"></span>Skylark Reelworks</div>

    <ul class="contact-list">
      <li>
        <svg class="contact-icon" viewBox="0 0 12 12" aria-hidden="true"><path d="M2.5 1 L4.5 1 L5.2 3.5 L4 4.5 C4.6 5.9 6.1 7.4 7.5 8 L8.5 6.8 L11 7.5 L11 9.5 C11 10.3 10.3 11 9.5 11 C5 11 1 7 1 2.5 C1 1.7 1.7 1 2.5 1 Z" fill="var(--orange)"/></svg>
        614-502-7738
      </li>
      <li>
        <svg class="contact-icon" viewBox="0 0 12 12" aria-hidden="true"><circle cx="6" cy="6" r="5" fill="none" stroke="var(--orange)" stroke-width="1.4"/><path d="M1 6 H11 M6 1 C3.5 3.5 3.5 8.5 6 11 M6 1 C8.5 3.5 8.5 8.5 6 11" fill="none" stroke="var(--orange)" stroke-width="1"/></svg>
        www.skylarkreelworks.example
      </li>
      <li>
        <svg class="contact-icon" viewBox="0 0 12 12" aria-hidden="true"><rect x="1" y="2.5" width="10" height="7" rx="1" fill="none" stroke="var(--orange)" stroke-width="1.4"/><path d="M1.5 3 L6 6.5 L10.5 3" fill="none" stroke="var(--orange)" stroke-width="1.2"/></svg>
        info@skylarkreelworks.example
      </li>
    </ul>

    <div class="holder">
      <h1 class="holder-name"><span class="holder-first">Owen</span> <span class="holder-last">Tarrick</span></h1>
      <p class="holder-role">Owner</p>
    </div>

    <p class="credentials">NRD Certified Remote Pilot<br>Fully Insured</p>
  </section>

  <section class="card card-back" aria-label="Business card back">
    <div class="brand"><span class="brand-mark"></span>Skylark Reelworks</div>
  </section>

</main>
</body>
</html>
```